12+4 box dietary supplements Vasquorinel(4), Marlocet(12)

Update design for 2 different groups of drugs in one concept with the previous 12 designs in the previous competition. In addition to the packaging design, 2 separate brochure designs for these groups must be made. A4 printable brochure for each individual page
Updates

Низкое качество дизайна

Target Market(s)

dietary supplements

Industry/Entity Type

Medic

```html
<!DOCTYPE html>
<html lang="en">
<head>
<meta charset="utf-8">
<title>Solvera Vasquorinel VQ1 – Brochure Spread</title>
<link href="https://fonts.googleapis.com/css2?family=Poppins:wght@300;400;500;600;700;800&display=swap" rel="stylesheet">
<style>
  :root{
    --backdrop:#58595b;
    --green:#5c9a1c;
    --green-dark:#3f7d0e;
    --green-light:#7fb52c;
    --ink:#1f2a1a;
    --ink-soft:#3a3a3a;
    --paper:#eeeff0;
    --white:#ffffff;
  }
  *{box-sizing:border-box;margin:0;padding:0}
  html,body{width:1200px;height:900px;overflow:hidden}
  body{background:var(--backdrop);font-family:"Poppins",sans-serif;position:relative}

  .spread{position:absolute;left:40px;top:54px;width:1120px;height:792px;display:flex;box-shadow:0 10px 30px rgba(0,0,0,.35)}
  .page{width:560px;height:792px;position:relative;overflow:hidden}

  /* Left page */
  .page--about{background:linear-gradient(100deg,var(--green-dark) 0%,var(--green) 45%,var(--green-light) 75%,var(--green) 100%);color:var(--white);padding:70px 48px 40px 56px}
  .about-title{font-weight:300;font-size:44px;line-height:1;letter-spacing:.5px}
  .about-subtitle{font-weight:500;font-size:22px;color:var(--ink);margin-top:6px;letter-spacing:.3px}
  .faq{margin-top:40px;display:flex;flex-direction:column;gap:24px}
  .faq-item h3{font-weight:600;font-size:13.5px;margin-bottom:4px}
  .faq-item p{font-weight:300;font-size:9.3px;line-height:1.45}

  /* Right page */
  .page--product{background:var(--paper);color:var(--ink-soft)}
  .hero-photo{position:absolute;left:0;top:0;width:560px;height:320px;background:linear-gradient(160deg,#6c5a34 0%,#9b7a3e 35%,#c9a85a 60%,#7f8f4a 85%,#5a6a30 100%)}
  .hero-fade{position:absolute;left:0;top:250px;width:560px;height:90px;background:linear-gradient(180deg,rgba(238,239,240,0) 0%,var(--paper) 80%)}
  .product-box{position:absolute;left:70px;top:180px;width:220px;height:130px;background:linear-gradient(180deg,#f4f4f4 0%,#f4f4f4 55%,var(--green-light) 55%,var(--green) 100%);border-radius:3px;box-shadow:0 12px 18px rgba(0,0,0,.25)}
  .badge{position:absolute;left:442px;top:250px;width:58px;height:58px;border-radius:50%;background:var(--green)}
  .badge svg{position:absolute;left:14px;top:14px}

  .product-heading{position:absolute;right:48px;top:322px;text-align:right}
  .product-heading .brand{font-weight:400;font-size:26px;color:var(--ink);line-height:1.1}
  .product-heading .name{font-weight:700;font-size:28px;color:var(--green);line-height:1.1}
  .heading-rule{position:absolute;left:56px;top:400px;width:456px;height:1.5px;background:var(--green)}

  .application{position:absolute;left:56px;top:414px;font-size:11.5px}
  .label{font-weight:700;color:var(--green);font-size:12px;text-transform:uppercase}
  .application .system{font-weight:500;color:var(--ink)}

  .ingredients{position:absolute;left:56px;top:470px;width:260px;font-size:10.2px;line-height:1.45}
  .ingredients .label{margin-bottom:4px}
  .group{margin-bottom:14px}
  .group h4{font-weight:600;color:var(--ink);font-size:10.5px;position:relative;padding-left:9px}
  .group h4::before{content:"";position:absolute;left:0;top:5px;width:5px;height:5px;border-radius:50%;background:var(--green)}
  .group li{list-style:none;padding-left:9px;font-weight:400}
  .group li::before{content:"• "}

  .actives{position:absolute;left:316px;top:460px;width:220px;font-size:10.2px;line-height:1.5}
  .actives .intro{padding-left:9px}

  .seniors-photo{position:absolute;left:388px;top:600px;width:156px;height:156px;border-radius:50%;background:radial-gradient(circle at 50% 40%,#c7b09a 0%,#8fae6a 55%,#6a8f45 100%)}

  .forms{position:absolute;left:56px;top:700px;display:flex;gap:26px;align-items:flex-end}
  .form-tag{border:2px solid var(--green);border-radius:4px;overflow:hidden;text-align:center}
  .form-tag .tag-head{background:var(--green);color:var(--white);font-size:8.5px;font-weight:600;padding:3px 10px;text-transform:uppercase}
  .form-tag .tag-body{font-weight:800;font-size:14px;color:var(--ink);padding:3px 10px;background:var(--white)}
  .packing .tag-body{display:flex;align-items:center;gap:6px;font-size:13px}
  .packing small{font-size:5.5px;font-weight:600;line-height:1;text-align:left}
  .packing .divider{width:1.5px;height:14px;background:var(--ink)}
</style>
</head>
<body>
<main class="spread">
  <section class="page page--about">
    <h1 class="about-title">ABOUT SOLVERA</h1>
    <h2 class="about-subtitle">VASQUORINEL SERIES</h2>

    <div class="faq">
      <article class="faq-item">
        <h3>What is vasquorinel?</h3>
        <p>Vasquorinel is a combination of 5 types of active ingredients – prebiotics, probiotics, postbiotics, parabiotics and active pharmaceutical ingredients.</p>
      </article>
      <article class="faq-item">
        <h3>What is prebiotic?</h3>
        <p>Prebiotics are non-digestible fibers that promote the growth of beneficial bacteria in the gut. They can be found in foods like garlic, onions, bananas, and whole grains. Prebiotics help improve digestion and overall gut health by nourishing the good bacteria in our intestines. Including prebiotic-rich foods or supplements in the diet can also support a healthy immune system and reduce inflammation in the body.</p>
      </article>
      <article class="faq-item">
        <h3>What is probiotic?</h3>
        <p>Probiotics are live bacteria and yeasts that are good for human health, especially the digestive system. They are often referred to as "good" or "friendly" bacteria because they help keep your gut healthy. Probiotics can be found in certain foods, such as yogurt, kefir, and sauerkraut, as well as in supplement form. Research has shown that probiotics may help with various digestive issues and boost the immune system.</p>
      </article>
      <article class="faq-item">
        <h3>What is postbiotic?</h3>
        <p>Postbiotics are non-viable bacterial products or metabolic byproducts that have beneficial effects on the host. These compounds can include short-chain fatty acids, enzymes, and peptides that contribute to overall gut health and immune function. Postbiotics are gaining attention in the field of gut health and are believed to play a crucial role in maintaining a healthy microbiome. Research suggests that postbiotics can help reduce inflammation, improve digestion, and support the body's natural defense mechanisms.</p>
      </article>
      <article class="faq-item">
        <h3>What is parabiotic?</h3>
        <p>Parabiotics are also referred to as paraprobiotics, ghost probiotics, or inactivated probiotics. It is a term used to describe inactivated microbial cells, either intact or broken, that belong to the cells of probiotics or other beneficial microorganisms. These inactivated cells still have beneficial effects on the host by interacting with the immune system and promoting a healthy gut microbiome. Parabiotics are gaining attention for their potential therapeutic applications in various health conditions. Research on parabiotics has shown promising results in areas such as improving gut health, reducing inflammation, and enhancing immune function. The use of parabiotics may offer a new approach to supporting overall health and wellness through the manipulation of the gut microbiome.</p>
      </article>
    </div>
  </section>

  <section class="page page--product">
    <div class="hero-photo" role="img" aria-label="Photo of a joyful young woman riding a bicycle through a sunlit autumn park, with virus particles floating nearby"></div>
    <div class="hero-fade"></div>
    <div class="product-box" role="img" aria-label="Product box of Solvera Vasquorinel VQ1 immune system complex, white and green"></div>
    <div class="badge">
      <svg width="30" height="30" viewBox="0 0 30 30" fill="none" stroke="#fff" stroke-width="1.8">
        <path d="M15 3 L25 8 V15 C25 21 20 25 15 27 C10 25 5 21 5 15 V8 Z"/>
        <circle cx="15" cy="15" r="4"/>
      </svg>
    </div>

    <div class="product-heading">
      <div class="brand">SOLVERA</div>
      <div class="name">VASQUORINEL VQ1</div>
    </div>
    <div class="heading-rule"></div>

    <div class="application">
      <div class="label">Main application:</div>
      <div><span class="system">IMMUNE SYSTEM</span> – immunomodulation, viral infections, allergies</div>
    </div>

    <div class="ingredients">
      <div class="label">Ingredients:</div>
      <div class="group">
        <h4>Probiotics</h4>
        <ul><li>300 mg of fructooligosaccharides (FOS)</li></ul>
      </div>
      <div class="group">
        <h4>Probiotics – 10 billion CFU blend</h4>
        <ul>
          <li>Bifidobacterium: bifidium, breve, longum</li>
          <li>Lactobacillus: acidophilus, casei, fermentum, plantarum, reuteri, rhamnosus</li>
        </ul>
      </div>
      <div class="group">
        <h4>Postbiotics and parabiotics</h4>
        <ul><li>100 mg proprietary blend of postbiotics and parabiotics</li></ul>
      </div>
    </div>

    <div class="actives">
      <div class="group">
        <h4>Active pharmaceutical ingredients</h4>
        <div class="intro">300 mg of proprietary blend</div>
        <ul>
          <li>Liposomal astragalus extract</li>
          <li>Liposomal Korean ginseng extract</li>
          <li>Liposomal Siberian ginseng extract</li>
          <li>Black elderberry extract</li>
          <li>Echinacea extract</li>
        </ul>
      </div>
    </div>

    <div class="seniors-photo" role="img" aria-label="Photo of a happy senior couple outdoors, the woman riding piggyback"></div>

    <div class="forms">
      <div class="form-tag">
        <div class="tag-head">Available forms</div>
        <div class="tag-body">30 CAPSULE</div>
      </div>
      <div class="form-tag packing">
        <div class="tag-head">Packing forms</div>
        <div class="tag-body">30 <small>CAPSULES<br>PER BOX</small><span class="divider"></span>15 <small>CAPSULES<br>PER BOX</small></div>
      </div>
    </div>
  </section>
</main>
</body>
</html>
```